Business Card Design

We need a business card designed for our new company. Prefer a black card with white logo & writing.

Contact Information for Business Card

Ted Galloway, address: 7-4812 Fernhollow Road, Abbotsford, BC, V3K 8R2, Office Phone: 604-712-3390, Cell: 604-947-2164, Email: ted@resinworkshub.ca

Colors

Designer to choose only greyscale colors for use in the design.

```html
<!DOCTYPE html>
<html lang="en">
<head>
<meta charset="utf-8">
<title>Resin Works Hub — Business Card</title>
<link href="https://fonts.googleapis.com/css2?family=Poppins:wght@300;400;700&display=swap" rel="stylesheet">
<style>
  :root {
    --page-bg: #232325;
    --card-bg: #1d1d1f;
    --card-edge: #2c2c2f;
    --ink: #ffffff;
    --ink-soft: #e6e6e6;
    --ink-dark: #1d1d1f;
    --foil: #b9b9bc;
  }
  * { box-sizing: border-box; margin: 0; padding: 0; }
  html, body {
    width: 1200px; height: 711px; overflow: hidden;
    background: var(--page-bg);
    font-family: "Poppins", sans-serif;
    color: var(--ink);
  }
  .stage {
    position: relative; width: 1200px; height: 711px;
  }
  .card {
    position: absolute; top: 75px; width: 330px; height: 560px;
    background: var(--card-bg);
    border: 1px solid var(--card-edge);
    border-radius: 22px;
    box-shadow: 0 14px 30px rgba(0,0,0,.55);
    overflow: hidden;
  }
  .card--front { left: 230px; }
  .card--back { left: 640px; }

  /* front: brand name in foil grey */
  .front-brand {
    position: absolute; left: 0; right: 0; top: 250px;
    text-align: center;
    font-weight: 700; font-size: 34px; line-height: 1.05;
    color: var(--foil);
    letter-spacing: 1px;
  }
  .front-brand .brand-mark {
    display: block; width: 14px; height: 14px; margin: 0 auto 14px;
    background: var(--foil); border-radius: 50%;
  }

  /* back */
  .back-brand {
    position: absolute; left: 0; right: 0; top: 58px;
    text-align: center;
    font-weight: 700; font-size: 30px; line-height: 1.05;
    color: var(--ink);
    letter-spacing: .5px;
  }
  .back-brand .brand-mark {
    display: block; width: 12px; height: 12px; margin: 0 auto 12px;
    border-radius: 50%; background: var(--ink);
  }
  .person {
    position: absolute; left: 0; right: 0; top: 250px; text-align: center;
  }
  .person__name { font-size: 30px; font-weight: 300; line-height: 1.1; }
  .person__name strong { font-weight: 700; }
  .person__role { font-size: 13px; font-weight: 400; color: var(--ink-soft); margin-top: 2px; }

  .dot-row { position: absolute; left: 0; width: 330px; height: 26px; display: block; }
  .contact {
    position: absolute; left: 0; right: 0; text-align: center;
    font-size: 13.5px; font-weight: 300; line-height: 1.45; color: var(--ink-soft);
  }
  .contact--lines { top: 352px; }
  .contact--address { top: 476px; }
</style>
</head>
<body>
<main class="stage">

  <section class="card card--front" aria-label="Card front">
    <div class="front-brand"><span class="brand-mark"></span>RESIN WORKS<br>HUB</div>
  </section>

  <section class="card card--back" aria-label="Card back">
    <div class="back-brand"><span class="brand-mark"></span>RESIN WORKS<br>HUB</div>

    <div class="person">
      <h1 class="person__name"><strong>Ted</strong> Galloway</h1>
      <p class="person__role">Founder &amp; CEO</p>
    </div>

    <!-- contact icon row -->
    <svg class="dot-row" style="top:318px" viewBox="0 0 330 26" aria-hidden="true">
      <g fill="#fff">
        <circle cx="6" cy="13" r="1.5"/><circle cx="18" cy="13" r="2"/><circle cx="32" cy="13" r="2.8"/>
        <circle cx="48" cy="13" r="3.6"/><circle cx="66" cy="13" r="4.4"/>
        <circle cx="98" cy="13" r="12"/><circle cx="130" cy="13" r="12"/>
        <circle cx="162" cy="13" r="12"/><circle cx="194" cy="13" r="12"/>
        <circle cx="226" cy="13" r="4.4"/><circle cx="244" cy="13" r="3.6"/>
        <circle cx="260" cy="13" r="2.8"/><circle cx="274" cy="13" r="2"/><circle cx="286" cy="13" r="1.5"/>
        <circle cx="298" cy="13" r="1.2"/><circle cx="310" cy="13" r="1"/><circle cx="322" cy="13" r="1"/>
      </g>
      <g fill="none" stroke="#1d1d1f" stroke-width="1.4" stroke-linecap="round">
        <!-- phone -->
        <path d="M93 8 q-2 2 0 6 q2 4 7 6 q3 1 4-1 l-2-2 q-1 1-2 0 q-3-2-4-4 q0-1 1-2 z"/>
        <!-- office phone -->
        <rect x="124" y="9" width="12" height="10" rx="1.5"/><path d="M127 9 v-3 h6 v3 M128 13 h4 M128 16 h4"/>
        <!-- email -->
        <rect x="155" y="8" width="14" height="10" rx="1"/><path d="M155 9 l7 5 l7-5"/>
        <!-- globe -->
        <circle cx="194" cy="13" r="6.5"/><path d="M187.5 13 h13 M194 6.5 q-4 6.5 0 13 q4-6.5 0-13"/>
      </g>
    </svg>

    <div class="contact contact--lines">
      604-712-3390<br>604-947-2164<br>www.resinworkshub.ca<br>ted@resinworkshub.ca
    </div>

    <!-- address pin row -->
    <svg class="dot-row" style="top:444px" viewBox="0 0 330 26" aria-hidden="true">
      <g fill="#fff">
        <circle cx="8" cy="13" r="1.2"/><circle cx="22" cy="13" r="1.6"/><circle cx="38" cy="13" r="2.2"/>
        <circle cx="56" cy="13" r="3"/><circle cx="76" cy="13" r="3.8"/><circle cx="98" cy="13" r="4.6"/>
        <circle cx="122" cy="13" r="5.4"/><circle cx="165" cy="13" r="12"/>
        <circle cx="208" cy="13" r="5.4"/><circle cx="232" cy="13" r="4.6"/><circle cx="254" cy="13" r="3.8"/>
        <circle cx="274" cy="13" r="3"/><circle cx="292" cy="13" r="2.2"/><circle cx="308" cy="13" r="1.6"/>
        <circle cx="322" cy="13" r="1.2"/>
      </g>
      <path d="M165 20 q-5-5-5-9 a5 5 0 0 1 10 0 q0 4-5 9 z" fill="none" stroke="#1d1d1f" stroke-width="1.4"/>
      <circle cx="165" cy="11" r="1.6" fill="#1d1d1f"/>
    </svg>

    <div class="contact contact--address">
      7-4812 Fernhollow Road,<br>Abbotsford, BC, V3K 8R2.
    </div>

    <svg class="dot-row" style="top:524px" viewBox="0 0 330 26" aria-hidden="true">
      <g fill="#fff">
        <circle cx="10" cy="13" r="1.2"/><circle cx="30" cy="13" r="1.8"/><circle cx="52" cy="13" r="2.4"/>
        <circle cx="76" cy="13" r="3"/><circle cx="102" cy="13" r="3.6"/><circle cx="130" cy="13" r="4.2"/>
        <circle cx="165" cy="13" r="4.8"/><circle cx="200" cy="13" r="4.2"/><circle cx="228" cy="13" r="3.6"/>
        <circle cx="254" cy="13" r="3"/><circle cx="278" cy="13" r="2.4"/><circle cx="300" cy="13" r="1.8"/>
        <circle cx="320" cy="13" r="1.2"/>
      </g>
    </svg>
  </section>

</main>
</body>
</html>
```